Marlowick Cafe' eLiquid Label - retro, trendy design

Need a 1.5"x3" label designed for an eLiquid bottle. I like the distressed retro diner look. Feel free to take creative license on logo, images etc. Attaching a mockup I did just to give you an idea of what look I want - the attached concept has all textual elements required....want retro trendy....corvanel-ish look and personality...warm colors...high contrasts. attached Nolse image is the mockup I want redesigned.

Target Market(s)

eclectic

Industry/Entity Type

Cafe

Font styles to use
Serif
Decorative

Requirements
Must have
• text elements from uploaded sample - 1.5x3 inch high res
Nice to have
• incorporate QM logo somewhere in the design - attached

```html
<!DOCTYPE html>
<html lang="en">
<head>
<meta charset="utf-8">
<title>Marlowick Vapor – Label Options</title>
<link rel="stylesheet" href="https://fonts.googleapis.com/css2?family=Cinzel:wght@500;700&family=Roboto+Condensed:wght@400;700&family=Roboto:wght@400;500;700&display=swap">
<style>
  :root {
    --page: #ffffff;
    --label-black: #141414;
    --label-dark: #1d1d1d;
    --gold: #b8892c;
    --gold-light: #e8d6a6;
    --gold-pale: #f4ead0;
    --cream: #f3ecd9;
    --white: #ffffff;
    --soft-grey: #cfcfcf;
    --ink: #2a2116;
    --divider: #2b1d16;
    --option-red: #e5141b;
  }
  * { box-sizing: border-box; margin: 0; padding: 0; }
  html, body { width: 1200px; height: 1000px; overflow: hidden; background: var(--page); }
  .canvas { position: relative; width: 1200px; height: 1000px; background: var(--page); font-family: "Roboto", Arial, sans-serif; }

  .divider { position: absolute; left: 0; top: 490px; width: 1200px; height: 12px; background: var(--divider); }

  .option-title {
    position: absolute; width: 400px; text-align: center;
    font-family: "Roboto", Arial, sans-serif; font-weight: 700; font-size: 40px;
    color: var(--option-red); letter-spacing: 1px;
  }

  .label {
    position: absolute; overflow: hidden;
    background: radial-gradient(ellipse at center, var(--label-dark) 0%, var(--label-black) 75%);
    color: var(--white);
  }
  .label-pattern { position: absolute; inset: 0; background: radial-gradient(ellipse at center, #222 0%, #121212 80%); }
  .top-band { position: absolute; left: 0; top: 0; width: 100%; height: 8px;
    background: linear-gradient(90deg, #9a7224, #d4b066, #a27a2a); }
  .bottom-band { position: absolute; left: 0; bottom: 0; width: 100%; height: 47px;
    background: linear-gradient(90deg, #a87c26 0%, #e6d3a0 30%, var(--gold-pale) 50%, #e6d3a0 70%, #a87c26 100%);
    display: flex; align-items: center; justify-content: center;
    font-family: "Roboto", Arial, sans-serif; font-weight: 700; font-size: 20px; color: var(--ink); }
  .bottom-band .star { color: var(--gold); margin: 0 8px; font-size: 16px; }

  .brand { position: absolute; width: 100%; text-align: center; font-family: "Roboto Condensed", Arial Narrow, sans-serif; font-weight: 700; color: var(--cream); letter-spacing: .5px; }
  .tagline { position: absolute; width: 100%; text-align: center; font-family: "Roboto Condensed", Arial Narrow, sans-serif; letter-spacing: .5px; }

  .brand-mark { position: absolute; display: flex; align-items: center; justify-content: center;
    width: 100px; height: 100px; border-radius: 50%; border: 3px solid var(--gold); background: var(--label-black);
    font-family: "Roboto Condensed", Arial Narrow, sans-serif; font-weight: 700; font-size: 13px; color: var(--white); text-align: center; line-height: 1.2; }

  .flourish { position: absolute; height: 60px;
    background: linear-gradient(90deg, rgba(184,137,44,0) 0%, rgba(184,137,44,.75) 25%, rgba(184,137,44,.35) 50%, rgba(184,137,44,.75) 75%, rgba(184,137,44,0) 100%); }

  .flavor { position: absolute; width: 100%; text-align: center; font-family: "Cinzel", "Times New Roman", serif; font-weight: 500; color: var(--white); letter-spacing: 4px; }
  .flavor-rule { position: absolute; height: 1px; background: var(--soft-grey); }
  .strength { position: absolute; width: 100%; text-align: center; font-size: 15px; font-weight: 500; color: var(--white); }

  .ingredients {
    position: absolute; writing-mode: vertical-rl; height: 315px;
    font-family: "Roboto", Arial, sans-serif; font-size: 8.6px; line-height: 12px; text-transform: uppercase; color: var(--white);
  }
  .ingredients .lead { text-transform: none; font-weight: 700; font-size: 9.5px; margin-left: 4px; }
  .ingredients p { margin-left: 6px; }

  .lot { position: absolute; writing-mode: vertical-rl; transform: rotate(180deg); font-size: 14px; color: var(--white); }
  .site { position: absolute; writing-mode: vertical-rl; transform: rotate(180deg); font-size: 14px; font-weight: 700; color: var(--gold); letter-spacing: .5px; }
  .origin { position: absolute; font-size: 13px; color: var(--white); }
</style>
</head>
<body>
<main class="canvas">

  <!-- Option 1 -->
  <section class="label" style="left:387px; top:37px; width:764px; height:382px;">
    <div class="label-pattern" role="img" aria-label="Dark damask wallpaper pattern"></div>
    <div class="top-band"></div>
    <div class="ingredients" style="left:8px; top:18px; width:112px;">
      <span class="lead">Vegetable Glycerin, Propylene Glycol, Flavoring, Nicotine</span>
      <p>Prop 65: keep out of children and pets. AMPC poison hotline: 800-555-0142. Nicotin is a chemical known in the state of California</p>
      <p>to cause birth defects and other reproductive harm. Nicotine is an addictive chemical derived from tobaco. 18+ only.</p>
    </div>
    <div class="brand" style="top:30px; font-size:38px;">MARLOWICK VAPOR</div>
    <div class="tagline" style="top:72px; font-size:15px; color:var(--gold);">ULTRA-PREMIUM MOD GREASE</div>
    <div class="flourish" role="img" aria-label="Gold baroque scroll ornament" style="left:198px; top:168px; width:380px;"></div>
    <div class="brand-mark" style="left:338px; top:108px;">MARLOWICK<br>VAPOR</div>
    <div class="flavor" style="top:238px; font-size:50px;">NOLSEMISU</div>
    <div class="flavor-rule" style="left:203px; top:293px; width:375px;"></div>
    <div class="strength" style="top:312px;">12 mg Nicotine</div>
    <div class="lot" style="left:652px; top:95px;">Lot Number: 12345</div>
    <div class="site" style="left:730px; top:100px;">WWW.MARLOWICK.COM</div>
    <div class="origin" style="left:634px; top:308px;">Made in the USA</div>
    <div class="bottom-band">30 ml <span class="star">★</span> 70/30</div>
  </section>
  <div class="option-title" style="left:570px; top:430px;">OPTION-1</div>

  <div class="divider"></div>

  <!-- Option 2 -->
  <section class="label" style="left:385px; top:537px; width:760px; height:379px;">
    <div class="label-pattern" role="img" aria-label="Dark damask wallpaper pattern"></div>
    <div class="top-band"></div>
    <div class="ingredients" style="left:6px; top:18px; width:112px;">
      <span class="lead">Vegetable Glycerin, Propylene Glycol, Flavoring, Nicotine</span>
      <p>Prop 65: keep out of children and pets. AMPC poison hotline: 800-555-0142. Nicotin is a chemical known in the state of California</p>
      <p>to cause birth defects and other reproductive harm. Nicotine is an addictive chemical derived from tobaco. 18+ only.</p>
    </div>
    <div class="brand" style="top:32px; font-size:26px;">MARLOWICK VAPOR</div>
    <div class="tagline" style="top:63px; font-size:15px; color:var(--soft-grey);">ULTRA-PREMIUM MOD GREASE</div>
    <div class="flourish" role="img" aria-label="Gold baroque scroll ornament" style="left:190px; top:150px; width:380px;"></div>
    <div class="brand-mark" style="left:330px; top:102px;">MARLOWICK<br>VAPOR</div>
    <div class="flavor" style="top:234px; font-size:50px;">NOLSEMISU</div>
    <div class="flavor-rule" style="left:195px; top:289px; width:375px;"></div>
    <div class="strength" style="top:309px;">12 mg Nicotine</div>
    <div class="lot" style="left:653px; top:98px;">Lot Number: 12345</div>
    <div class="site" style="left:724px; top:75px;">WWW.MARLOWICK.COM</div>
    <div class="origin" style="left:630px; top:306px;">Made in the USA</div>
    <div class="bottom-band">30 ml <span class="star">★</span> 70/30</div>
  </section>
  <div class="option-title" style="left:567px; top:930px;">OPTION-2</div>

</main>
</body>
</html>
```